Business Card Design

We are a manufacturing and distribution company with most of our customer base being supermarkets. We have established brand guidelines that are attached.

```html
<!DOCTYPE html>
<html lang="en">
<head>
<meta charset="UTF-8">
<title>Corvanta Business Card</title>
<link href="https://fonts.googleapis.com/css2?family=Arimo:wght@400;700&display=swap" rel="stylesheet">
<style>
  :root {
    --backdrop: #2a2a2a;
    --card: #0b0b0b;
    --white: #ffffff;
    --soft-white: #e8e8e8;
    --red: #e31b23;
    --blue: #1a73c2;
    --divider: #4a4a4a;
  }
  * { margin: 0; padding: 0; box-sizing: border-box; }
  html, body { width: 1200px; height: 900px; overflow: hidden; }
  body {
    background: var(--backdrop);
    font-family: "Arimo", Arial, sans-serif;
    display: flex;
    align-items: center;
    justify-content: center;
    gap: 40px;
  }
  .card {
    width: 540px;
    height: 309px;
    background: var(--card);
    position: relative;
    overflow: hidden;
  }
  .wordmark {
    display: flex;
    align-items: center;
    gap: 12px;
    color: var(--soft-white);
    font-weight: 700;
    letter-spacing: 2px;
    text-transform: uppercase;
  }
  .wordmark__square {
    width: 22px;
    height: 22px;
    background: var(--red);
    flex: none;
  }

  /* Front: contact side */
  .card--front .wordmark {
    position: absolute;
    left: 40px;
    top: 130px;
    font-size: 34px;
  }
  .card--front .divider {
    position: absolute;
    left: 295px;
    top: 60px;
    width: 1px;
    height: 190px;
    background: var(--divider);
  }
  .details {
    position: absolute;
    left: 318px;
    top: 62px;
    color: var(--white);
  }
  .person__name {
    font-weight: 700;
    font-size: 17px;
    letter-spacing: 0.5px;
    text-transform: uppercase;
  }
  .person__first { color: var(--red); }
  .person__last { color: var(--blue); }
  .person__role {
    font-size: 13px;
    margin-top: 2px;
  }
  .contacts {
    list-style: none;
    margin-top: 16px;
    font-size: 13px;
  }
  .contacts li {
    display: flex;
    align-items: center;
    gap: 8px;
    height: 20px;
  }
  .contacts svg { width: 12px; height: 12px; flex: none; }
  .web-domain { color: var(--blue); }
  .address {
    margin-top: 16px;
    font-size: 13px;
    line-height: 1.45;
  }

  /* Back: brand side */
  .card--back {
    display: flex;
    align-items: center;
    justify-content: center;
  }
  .card--back .wordmark {
    font-size: 36px;
    color: var(--white);
  }
</style>
</head>
<body>

  <section class="card card--front">
    <div class="wordmark">
      <span class="wordmark__square"></span>
      <span>Corvanta</span>
    </div>

    <div class="divider"></div>

    <div class="details">
      <p class="person__name"><span class="person__first">Daniel</span> <span class="person__last">Hartley</span></p>
      <p class="person__role">Managing Director</p>

      <ul class="contacts">
        <li>
          <svg viewBox="0 0 24 24" fill="none" stroke="#e31b23" stroke-width="2.5" stroke-linecap="round" stroke-linejoin="round"><path d="M22 16.9v3a2 2 0 0 1-2.2 2 19.8 19.8 0 0 1-8.6-3.1 19.5 19.5 0 0 1-6-6A19.8 19.8 0 0 1 2.1 4.2 2 2 0 0 1 4.1 2h3a2 2 0 0 1 2 1.7c.1 1 .4 1.9.7 2.8a2 2 0 0 1-.5 2.1L8 9.9a16 16 0 0 0 6 6l1.3-1.3a2 2 0 0 1 2.1-.4c.9.3 1.8.6 2.8.7a2 2 0 0 1 1.7 2z"/></svg>
          <span>044-987 654 321</span>
        </li>
        <li>
          <svg viewBox="0 0 24 24"><rect x="1" y="4" width="22" height="16" fill="#e31b23"/><path d="M1 4l11 9 11-9" fill="none" stroke="#0b0b0b" stroke-width="2"/></svg>
          <span>hello@corvanta.com</span>
        </li>
        <li>
          <svg viewBox="0 0 24 24" fill="none" stroke="#e31b23" stroke-width="2"><circle cx="12" cy="12" r="10"/><ellipse cx="12" cy="12" rx="4.5" ry="10"/><path d="M2 12h20M4 6.5h16M4 17.5h16"/></svg>
          <span>www.<span class="web-domain">corvanta</span>.com</span>
        </li>
      </ul>

      <p class="address">18, Millbrook Trading Park<br>60218, Northland</p>
    </div>
  </section>

  <section class="card card--back">
    <div class="wordmark">
      <span class="wordmark__square"></span>
      <span>Corvanta</span>
    </div>
  </section>

</body>
</html>
```